Web design for new streaming audio service

We need a homepage design for a new streaming audio service. Our company is called Dunmoral, and we’re basically Vexlo for Audiobooks, Stand-Up Comedy, Lectures, Language Learning, etc. Essentially like Plumtrek for everything audio EXCEPT music.
You don’t have to code the homepage (Design Only), but it should include 3 different designs to work with 1) Web; 2) Phones; 3) Tablets.
Below is a link to a mockup of the web version which gives a good idea of what elements we want. This is just a mockup and we want you to improve it.
Once you download the mockup, please refer to the more detailed instructions below:
The following outlines the design project for the Dunmoral homepage. We have provided a rough mockup of the homepage layout that gives you a general idea of what we’re going for. There are a few elements that we are attached to, and many others where you have complete creative freedom to do whatever you think looks good.
The ZIP file includes the following:
* Mockup to see what we have in mind (dunmoral-homepage-mockup.jpg)
* Text used (dunmoral-homepage-text.txt)
* Raw image of actor (dunmoral-actor1.jpg)
* Raw images for samples (dunmoral-sample-[name].jpg)
Although we have only provided a mockup layout for the web version, we also need you to provide a mobile phone and a tablet version of the design also. It’s very possible the tablet version may be substantially similar to the web version, but the mobile phone version will likely be much different.
All of the raw files are included in the attached ZIP file. Please use our photographs and text as provided although cropping, sizing, etc. is flexible per the instructions below.
Display Requirements:
* Web Version - Minimum resolution 1024x768 (72 dpi) but should look good on 1920x1080 (72 dpi) - Page should be designed to scale to look acceptable in all resolutions in between.
* Phone Version - Minimum Zarno 4 - 640x960 (326 dpi) but should look good on Harlow Quasar T5 - 1920x1080 (441 dpi) - Page should be designed to scale to look acceptable in all resolutions and devices in between.
* Tablet Version - Minimum Bristly Ember QX 7” - 1280x800 (216 dpi) but should also look good on a Tavo Breeze - 2048x1536 (264 dpi) - Page should be designed to scale to look acceptable in all resolutions and devices in between.
Above the Fold - We want to make sure the Dunmoral logo, Member Login Link, Large Photo, Headline, Price, Button, and the first row of sample images are all “Above the fold”. As a general guideline, this means 600 pixels high on a 1024x768 72 dpi web screen. This requirement is less important on Phone versions.
Top Logo Bar - We want to retain the blue bar with the Dunmoral logo on the page, although we are open to a different size, shape and positioning if it greatly enhances the design. Please use the standard logo color, although you are welcome to use either the horizontal or vertical orientation of the logo based on your design.
Text color, font and size - Feel free to design the text in anyway you choose as long as the text is readable on the target platforms.
Buttons - Feel free to use any size, shape and colors for the buttons as long as they are obvious and clickable relative to the page. The only exception is the Chatterly button should follow the Chatterly color scheme and logo treatment (the mockup doesn’t seem 100% correct.)
Top Photograph - We want to retain the large photograph across the top of the screen although final shape and dimensions are flexible.
Size and shape of content samples (i.e. Audiobooks, Stand-Up Comedy, etc.) - Feel free to design the content samples in anyway you choose.
Three Sales Points (i.e. Listen on your Zarno…, All you can enjoy…, etc.) - The Three Sales Points are envisioned to each have a corresponding illustration which you should provide and have rights for. The placeholder is represented by a square next to the text. The color size and shape of these elements are flexible and can be designed in any way you choose.
Opt-in form - Feel free to design the opt-in form in anyway you choose as long as the text is readable and the interactivity is obvious on the target platforms.
Text links and copyright notice - Feel free to design the bottom of the page text links and copyright notice in anyway you choose.
Additional colors, graphic design elements, etc. - Feel free to use any additional colors, graphic design elements, etc. to support your design.
people who want to listen to audio through their mobile devices.
Graphic Design

```html
<!DOCTYPE html>
<html lang="en">
<head>
<meta charset="utf-8">
<title>Dunmoral – Unlimited Listening</title>
<link rel="stylesheet" href="https://fonts.googleapis.com/css2?family=Nunito+Sans:wght@400;600;700;800&display=swap">
<style>
  :root{
    --brand-blue:#4a9bc8;
    --deep-blue:#1d6892;
    --icon-blue:#1f6a95;
    --orange:#f5a01f;
    --red:#e23a2b;
    --ink:#333333;
    --muted:#5a5a5a;
    --band:#3d3d3d;
    --band-text:#cfcfcf;
    --page:#fbfaf9;
    --social:#2f4f8a;
    --white:#ffffff;
  }
  *{box-sizing:border-box;margin:0;padding:0}
  html,body{width:1200px;height:2171px;overflow:hidden}
  body{font-family:"Nunito Sans",Arial,sans-serif;background:var(--page);color:var(--ink);position:relative}
  .abs{position:absolute}

  /* header */
  .topbar{left:0;top:0;width:1200px;height:99px;background:var(--brand-blue)}
  .brand{left:38px;top:22px;display:flex;align-items:center;gap:12px;color:var(--white);font-weight:700;font-size:44px;line-height:1}
  .brand-dot{width:44px;height:44px;border-radius:50%;background:var(--white)}
  .login{left:1038px;top:29px;width:120px;height:40px;background:var(--orange);color:var(--white);font-weight:700;font-size:20px;display:flex;align-items:center;justify-content:center}

  /* hero */
  .hero-photo{left:0;top:99px;width:1200px;height:567px;
    background:linear-gradient(100deg,#5a6f86 0%,#9a7b63 18%,#c79b7c 32%,#d9c2ae 48%,#eeeae6 62%,#f7f6f5 100%)}
  .hero-title{left:773px;top:158px;font-size:41px;font-weight:800;color:var(--deep-blue);line-height:1.1}
  .hero-sub{left:773px;top:205px;font-size:40px;font-weight:400;color:var(--deep-blue);line-height:1.1}
  .hero-price{left:773px;top:272px;font-size:26px;font-weight:600;color:var(--red);line-height:1.4}
  .hero-price strong{font-size:41px;font-weight:700}
  .cta{background:var(--orange);color:var(--white);font-weight:700;display:flex;align-items:center;justify-content:center}
  .hero-cta{left:773px;top:336px;width:287px;height:64px;font-size:23px}
  .hero-note{left:773px;top:408px;font-size:20px;color:var(--ink)}

  /* samples */
  .section-title{left:0;width:1200px;text-align:center;font-size:32px;font-weight:600;color:var(--deep-blue)}
  .samples-title{top:706px}
  .tile{width:229px;height:124px}
  .tile-label{width:285px;text-align:center;font-size:18px;font-weight:700;color:var(--ink);letter-spacing:.2px}

  /* sales points */
  .points{left:0;top:1238px;width:1200px;height:351px;background:var(--band)}
  .point{width:360px;text-align:center}
  .point-icon{width:139px;height:139px;border-radius:50%;background:var(--icon-blue);margin:42px auto 0;display:flex;align-items:center;justify-content:center}
  .point-title{margin-top:26px;font-size:23px;font-weight:600;color:var(--white)}
  .point-text{margin-top:12px;font-size:17px;line-height:26px;color:var(--band-text)}

  /* trial */
  .trial-title{top:1647px}
  .trial-text{left:200px;top:1718px;width:800px;text-align:center;font-size:18px;line-height:33px;color:var(--muted)}
  .email{left:253px;top:1814px;width:350px;height:54px;border:1px solid #cfcfcf;background:var(--white);font-size:16px;color:#9a9a9a;padding:0 16px;display:flex;align-items:center}
  .access{left:625px;top:1815px;width:257px;height:52px;font-size:21px}
  .or{left:0;top:1892px;width:1200px;text-align:center;font-size:19px;color:#999}
  .social{left:475px;top:1942px;width:252px;height:48px;background:var(--social);border-radius:3px;display:flex;align-items:center;color:var(--white);font-size:17px;font-weight:600}
  .social-mark{width:50px;height:48px;border-right:1px solid rgba(255,255,255,.25);display:flex;align-items:center;justify-content:center}
  .social-mark span{width:18px;height:18px;background:var(--white)}
  .social-text{padding-left:18px}
  .trial-note{left:0;top:2004px;width:1200px;text-align:center;font-size:19px;font-weight:600;color:var(--red)}

  /* footer */
  .footer{left:0;top:2092px;width:1200px;height:79px;background:var(--band);color:var(--white);font-size:15px}
  .footer-links{left:56px;top:28px;display:flex;gap:0}
  .footer-links span{padding:0 12px;border-left:1px solid #888;line-height:16px}
  .footer-links span:first-child{padding-left:0;border-left:none}
  .copyright{right:56px;top:28px;line-height:16px}
</style>
</head>
<body>

<header class="abs topbar">
  <div class="abs brand"><span class="brand-dot"></span>Dunmoral</div>
  <div class="abs login">LOG IN</div>
</header>

<section>
  <div class="abs hero-photo" role="img" aria-label="Smiling young man wearing headphones, looking at his phone"></div>
  <h1 class="abs hero-title">Unlimited Listening!</h1>
  <p class="abs hero-sub">Where ever you are</p>
  <p class="abs hero-price">Only <strong>$9.99</strong> Per Month</p>
  <div class="abs cta hero-cta">Start Your Free Trail</div>
  <p class="abs hero-note">*Credit card not required</p>
</section>

<section>
  <h2 class="abs section-title samples-title">A sample of what you can listen to on Dunmoral</h2>

  <div class="abs tile" style="left:59px;top:806px;background:linear-gradient(135deg,#1e2a2c,#4f6d6a 55%,#e0c52a)" role="img" aria-label="Suspense novels audiobook cover"></div>
  <div class="abs tile" style="left:343px;top:806px;background:linear-gradient(135deg,#d8cfc0,#b43a2c 60%,#6a3a2a)" role="img" aria-label="Stand-up comedy album cover"></div>
  <div class="abs tile" style="left:627px;top:806px;background:linear-gradient(135deg,#1ea0e0,#1589cc)" role="img" aria-label="French language course cover"></div>
  <div class="abs tile" style="left:912px;top:806px;background:linear-gradient(135deg,#8a7a6a,#c9b59a 50%,#6d8aa0)" role="img" aria-label="Biography audiobook cover"></div>

  <div class="abs tile-label" style="left:31px;top:942px">AUDIO BOOKS</div>
  <div class="abs tile-label" style="left:315px;top:942px">STAND-UP COMEDY</div>
  <div class="abs tile-label" style="left:599px;top:942px">LANGUAGE LEARNING</div>
  <div class="abs tile-label" style="left:884px;top:942px">BIOGRAPHIES MEMORY</div>

  <div class="abs tile" style="left:59px;top:1016px;background:linear-gradient(180deg,#b34fa8,#d982c9 60%,#9a4a9a)" role="img" aria-label="Relaxation meditation cover"></div>
  <div class="abs tile" style="left:343px;top:1016px;background:linear-gradient(135deg,#3a1a0e,#b86a22 45%,#d9d2c8)" role="img" aria-label="Business training program cover"></div>
  <div class="abs tile" style="left:627px;top:1016px;background:linear-gradient(135deg,#6a1a14,#c24a3a 50%,#e8c8a0)" role="img" aria-label="Celebrity interview series cover"></div>
  <div class="abs tile" style="left:912px;top:1016px;background:linear-gradient(135deg,#7ac0e8,#d4ecf8 55%,#e05a5a)" role="img" aria-label="Elliptical fitness program cover"></div>

  <div class="abs tile-label" style="left:31px;top:1153px">GUIDED MEDIATION</div>
  <div class="abs tile-label" style="left:315px;top:1153px">BUSINESS TRAINING</div>
  <div class="abs tile-label" style="left:599px;top:1153px">CELEBRITIES INTERVIEWS</div>
  <div class="abs tile-label" style="left:884px;top:1153px">FITNESS PROGRAM</div>
</section>

<section class="abs points">
  <div class="abs point" style="left:17px;top:0">
    <div class="point-icon">
      <svg width="70" height="76" viewBox="0 0 70 76" fill="none" stroke="#fff" stroke-width="5">
        <rect x="4" y="4" width="44" height="62" rx="5"/>
        <rect x="40" y="30" width="24" height="42" rx="4" fill="#1f6a95"/>
        <circle cx="26" cy="58" r="1.5" fill="#fff"/>
      </svg>
    </div>
    <div class="point-title">Listen Anywhere</div>
    <div class="point-text">Listen on your Zarno, Tavo or<br>any Orbix devices</div>
  </div>
  <div class="abs point" style="left:424px;top:0">
    <div class="point-icon">
      <svg width="60" height="80" viewBox="0 0 60 80"><text x="30" y="66" text-anchor="middle" font-family="Nunito Sans, Arial, sans-serif" font-weight="800" font-size="78" fill="#fff">$</text></svg>
    </div>
    <div class="point-title">Low Pricing</div>
    <div class="point-text">All you can enjoy for low<br>monthly Price</div>
  </div>
  <div class="abs point" style="left:829px;top:0">
    <div class="point-icon">
      <svg width="60" height="60" viewBox="0 0 60 60" stroke="#fff" stroke-width="8" stroke-linecap="square"><path d="M8 8L52 52M52 8L8 52"/></svg>
    </div>
    <div class="point-title">No Obligation</div>
    <div class="point-text">No Obligation cancel at<br>anytime</div>
  </div>
</section>

<section>
  <h2 class="abs section-title trial-title">Start your free Trial, No Risk</h2>
  <p class="abs trial-text">You will get instant &amp; unlimited access to all the material on Dunmoral for 14 days. There is no obligation &amp; you can cancel at anytime.</p>
  <div class="abs email">Your email Address</div>
  <div class="abs cta access">Get Instant Access</div>
  <div class="abs or">— Or —</div>
  <div class="abs social"><div class="social-mark"><span></span></div><div class="social-text">Sign in with Chatterly</div></div>
  <p class="abs trial-note">*Credit card not required</p>
</section>

<footer class="abs footer">
  <div class="abs footer-links"><span>About</span><span>Help</span><span>Contact Us</span><span>Member Login</span><span>Privacy Policy</span><span>Terms of Service</span></div>
  <div class="abs copyright">© 2014 Dunmoral LLC - All Rights Reserved</div>
</footer>

</body>
</html>
```